Business card design Needed for new logo / Construction business, home extensions and new builds

We need a business card design using our new logo files which i will attach to this project :)

We are a small construction business specialising in home extensions, new builds and property development. We are very ambitious and would appreciate professional and elegant designs for our new business card.

Very serious about using the services on MakerQuarry and recently acquired our new logo from here :)

Please get involved, i will feedback when i can as i am very busy but can respond daily, thanks

Target Market(s)

People that want to build onto their houses, new building developments or adding too their existing property

Industry/Entity Type

Construction

Contact Information for Business Card

Renwick Tolliver Construction, Lionel Ashby (Managing Director), Tel 07822254961, email - info@renwick-tolliver, www.renwick-tolliver.co.uk

Colors

Designer to choose colors to be used in the design.

Requirements
Must have
• I like a deep grey on the back please. A lot of you have provided black from and back, try mixing things up a little. The black looks cool 😎 Thanks

```html
<!DOCTYPE html>
<html lang="en">
<head>
<meta charset="utf-8">
<title>Renwick Tolliver Construction – Business Card</title>
<link href="https://fonts.googleapis.com/css2?family=Montserrat:wght@400;600;700&display=swap" rel="stylesheet">
<style>
  :root {
    --stage: #2b2b2d;
    --card-grey: #38383d;
    --card-black: #1d1e1f;
    --gold: #e0a93a;
    --gold-light: #f5cf6e;
    --silver: #c9ccd1;
    --white: #f2f2f2;
  }
  * { margin: 0; padding: 0; box-sizing: border-box; }
  html, body { width: 1200px; height: 689px; overflow: hidden; }
  body {
    background: var(--stage);
    font-family: "Montserrat", sans-serif;
    position: relative;
  }
  .card {
    position: absolute;
    top: 190px;
    width: 540px;
    height: 309px;
    border-radius: 22px;
    overflow: hidden;
  }
  .card-front { left: 40px; background: var(--card-grey); }
  .card-back { left: 620px; background: var(--card-black); }
  .card-back .backdrop { position: absolute; inset: 0; }

  .brand-name {
    font-family: "Montserrat", sans-serif;
    font-weight: 600;
    color: var(--gold);
    text-transform: uppercase;
    text-align: center;
    letter-spacing: 0.12em;
    line-height: 1.3;
    display: flex;
    flex-direction: column;
    align-items: center;
    gap: 10px;
  }
  .brand-mark {
    width: 14px; height: 14px;
    background: var(--gold);
    border-radius: 50%;
  }
  .card-front .brand-name {
    position: absolute;
    left: 0; right: 0; top: 50%;
    transform: translateY(-50%);
    font-size: 26px;
  }
  .card-back .brand-name--side {
    position: absolute;
    left: 330px; width: 200px; top: 70px;
    font-size: 15px;
  }
  .card-back .brand-name--main {
    position: absolute;
    left: 34px; width: 230px; top: 38px;
    font-size: 15px;
    align-items: flex-start;
    text-align: left;
  }

  .contact-block {
    position: absolute;
    left: 34px; top: 142px;
  }
  .person-name {
    color: var(--gold);
    font-weight: 700;
    font-size: 24px;
    letter-spacing: 0.01em;
  }
  .person-role {
    color: var(--white);
    font-size: 13px;
    margin-top: 2px;
  }
  .contact-list {
    list-style: none;
    margin-top: 16px;
    display: flex;
    flex-direction: column;
    gap: 7px;
  }
  .contact-list li {
    display: flex;
    align-items: center;
    gap: 9px;
    color: var(--white);
    font-size: 13px;
  }
  .contact-list svg { width: 13px; height: 13px; flex: none; fill: var(--gold); }
</style>
</head>
<body>

  <section class="card card-front">
    <div class="brand-name">
      <span class="brand-mark"></span>
      <span>Renwick Tolliver<br>Construction</span>
    </div>
  </section>

  <section class="card card-back">
    <svg class="backdrop" viewBox="0 0 540 309" width="540" height="309">
      <defs>
        <linearGradient id="goldBand" x1="0" y1="0" x2="1" y2="1">
          <stop offset="0" stop-color="#b9862a"/>
          <stop offset="0.5" stop-color="#f5cf6e"/>
          <stop offset="1" stop-color="#d69b2c"/>
        </linearGradient>
        <linearGradient id="silverBand" x1="0" y1="0" x2="0" y2="1">
          <stop offset="0" stop-color="#8d9095"/>
          <stop offset="0.5" stop-color="#e4e6ea"/>
          <stop offset="1" stop-color="#9a9ca1"/>
        </linearGradient>
      </defs>
      <circle class="band-gold" cx="612" cy="104" r="300" fill="url(#goldBand)"/>
      <circle class="band-silver" cx="604" cy="98" r="296" fill="url(#silverBand)"/>
      <circle class="panel-grey" cx="606" cy="94" r="284" fill="#38383d"/>
    </svg>

    <div class="brand-name brand-name--side">
      <span>Renwick Tolliver<br>Construction</span>
    </div>

    <div class="brand-name brand-name--main">
      <span class="brand-mark"></span>
    </div>

    <div class="contact-block">
      <p class="person-name">Lionel Ashby</p>
      <p class="person-role">Managing Director</p>
      <ul class="contact-list">
        <li>
          <svg viewBox="0 0 16 16"><path d="M3 1h3l1.5 4-2 1.2a9 9 0 0 0 4.3 4.3L11 8.5l4 1.5v3a2 2 0 0 1-2 2C6.4 15 1 9.6 1 3a2 2 0 0 1 2-2z"/></svg>
          07822254961
        </li>
        <li>
          <svg viewBox="0 0 16 16"><path d="M1 3h14v10H1z M1 3l7 6 7-6" fill="none" stroke="#e0a93a" stroke-width="1.8"/></svg>
          info@renwick-tolliver
        </li>
        <li>
          <svg viewBox="0 0 16 16"><circle cx="8" cy="8" r="6.5" fill="none" stroke="#e0a93a" stroke-width="1.6"/><path d="M1.5 8h13M8 1.5c-3 3.5-3 9.5 0 13M8 1.5c3 3.5 3 9.5 0 13" fill="none" stroke="#e0a93a" stroke-width="1.2"/></svg>
          www.renwick-tolliver.co.uk
        </li>
      </ul>
    </div>
  </section>

</body>
</html>
```